The quiet harbor with an elephant incorporated in the background

Target Market(s)

Real estate

Industry/Entity Type

Real Estate

Contact Information for Business Card

On back on want my name & number
In front I want the business name, "the quiet harbor", below to say staging & design

Logo Text

The quiet harbor

Font styles to use
Serif

Colors
000000

Requirements
Must have
• I want an elephant behind the writing in gold transperant

```html
<!DOCTYPE html>
<html lang="en">
<head>
<meta charset="UTF-8">
<title>The Quiet Harbor – Business Card</title>
<link href="https://fonts.googleapis.com/css2?family=Cormorant+Garamond:wght@500;600;700&display=swap" rel="stylesheet">
<style>
  :root {
    --backdrop: #2b2b2b;
    --card: #1b1b1b;
    --gold: #b8954a;
    --gold-light: #d8b866;
    --gold-deep: #8f6a25;
    --white: #f4f4f4;
  }
  * { margin: 0; padding: 0; box-sizing: border-box; }
  html, body {
    width: 1200px;
    height: 1000px;
    overflow: hidden;
    background: var(--backdrop);
    font-family: "Cormorant Garamond", Georgia, serif;
  }
  .canvas {
    position: relative;
    width: 1200px;
    height: 1000px;
  }
  .card {
    position: absolute;
    left: 220px;
    width: 760px;
    height: 420px;
    background: var(--card);
    box-shadow: 0 10px 30px rgba(0, 0, 0, 0.5);
  }
  .card--front { top: 50px; }
  .card--back { top: 530px; }

  .brand {
    position: absolute;
    left: 50%;
    top: 50%;
    transform: translate(-50%, -50%);
    display: flex;
    flex-direction: column;
    align-items: center;
  }
  .brand-frame {
    width: 400px;
    height: 86px;
    border: 2px solid var(--gold);
    display: flex;
    align-items: center;
    justify-content: center;
  }
  .brand-name {
    color: var(--white);
    font-size: 23px;
    font-weight: 600;
    letter-spacing: 6px;
    text-transform: uppercase;
    white-space: nowrap;
  }
  .brand-tagline {
    margin-top: 16px;
    color: var(--gold);
    font-size: 15px;
    font-weight: 600;
    letter-spacing: 5px;
    text-transform: uppercase;
    white-space: nowrap;
  }

  .contact {
    position: absolute;
    left: 80px;
    top: 255px;
  }
  .contact__name {
    color: var(--gold);
    font-size: 40px;
    font-weight: 700;
    letter-spacing: 1px;
    text-transform: uppercase;
    line-height: 1.05;
    white-space: nowrap;
  }
  .contact__role {
    color: var(--gold);
    font-size: 20px;
    font-weight: 600;
    margin-top: 2px;
  }
  .contact__phone {
    color: var(--white);
    font-size: 21px;
    font-weight: 600;
    margin-top: 14px;
    white-space: nowrap;
  }
  .contact__label { color: var(--gold); }

  .elephant-art {
    position: absolute;
    left: 480px;
    top: 215px;
    width: 250px;
    height: 185px;
  }
</style>
</head>
<body>
<main class="canvas">
  <section class="card card--front">
    <div class="brand">
      <div class="brand-frame">
        <span class="brand-name">The Quiet Harbor</span>
      </div>
      <p class="brand-tagline">Staging &amp; Design</p>
    </div>
  </section>

  <section class="card card--back">
    <div class="contact">
      <p class="contact__name">Daniel Marsh</p>
      <p class="contact__role">Owner</p>
      <p class="contact__phone"><span class="contact__label">P:</span> +000 555 010 246</p>
    </div>
    <svg class="elephant-art" viewBox="0 0 250 185" role="img" aria-label="Gold elephant figure with raised trunk">
      <defs>
        <radialGradient id="goldGlow" cx="50%" cy="50%" r="55%">
          <stop offset="0%" style="stop-color: var(--gold-light); stop-opacity: 0.85"/>
          <stop offset="60%" style="stop-color: var(--gold); stop-opacity: 0.55"/>
          <stop offset="100%" style="stop-color: var(--gold-deep); stop-opacity: 0"/>
        </radialGradient>
      </defs>
      <rect width="250" height="185" fill="url(#goldGlow)"/>
    </svg>
  </section>
</main>
</body>
</html>
```